Bork Ventures, Inc. Website redesign

Revamp the website, it is old and outdated. www.borkventuresinc.example

Target Market(s)

Information Technology Consulting and Staffing

Coding

Coded - Design and coding required

Number of Pages Required

5+ page

Colors

Designer to choose colors to be used in the design.

Requirements
Must have
• Outlined text boxes just like from the Tolvane.example site. A clean look

```html
<!DOCTYPE html>
<html lang="en">
<head>
<meta charset="utf-8">
<title>Bork Ventures, Inc.</title>
<link href="https://fonts.googleapis.com/css2?family=Poppins:wght@500;600;700;800&family=Roboto:wght@400;500&display=swap" rel="stylesheet">
<style>
:root{
  --red:#a01c2e;
  --ink:#333333;
  --text:#4a4a4a;
  --muted:#5a5a5a;
  --page:#f3f2f3;
  --card:#ffffff;
  --dark:#3a3a3a;
  --rule:#5c5c5c;
  --fb:#3b5998;
  --li:#1d2a6b;
}
*{margin:0;padding:0;box-sizing:border-box}
html,body{width:1200px;height:3637px;overflow:hidden}
body{position:relative;background:var(--page);font-family:'Roboto',sans-serif;color:var(--text)}
.abs{position:absolute}
.heading{font-family:'Poppins',sans-serif;font-weight:700;color:var(--ink)}
.btn{position:absolute;background:var(--red);color:#fff;font-family:'Poppins',sans-serif;font-weight:600;display:flex;align-items:center;justify-content:center;box-shadow:0 3px 6px rgba(0,0,0,.15)}

/* header */
.site-header{left:0;top:0;width:1200px;height:118px;background:#fff}
.brand{display:flex;align-items:center;gap:10px;font-family:'Poppins',sans-serif;font-weight:800;font-size:30px;letter-spacing:1px;color:var(--ink)}
.brand-square{width:26px;height:26px;background:var(--red)}
.follow{left:678px;top:34px;font-size:13px;color:var(--ink);display:flex;align-items:center;gap:8px}
.dot{width:24px;height:24px;border-radius:50%;display:inline-block}
.dot.fb{background:var(--fb)}.dot.li{background:var(--li)}
.call-icon{left:858px;top:22px;width:38px;height:38px;border:2px solid var(--red);border-radius:50%;display:flex;align-items:center;justify-content:center}
.call-label{left:907px;top:20px;font-size:13px;color:var(--ink)}
.call-number{left:907px;top:37px;font-size:25px;color:var(--red)}
.main-nav{left:496px;top:81px;display:flex;gap:28px;font-size:15px;color:var(--ink)}
.main-nav .active{color:var(--red);font-weight:500;border-bottom:2px solid var(--red)}

/* hero */
.hero-title{left:757px;top:258px;font-family:'Poppins',sans-serif;font-weight:800;font-size:47px;line-height:56px;color:#fff}
.slide-arrow{top:334px;width:34px;height:38px;background:#fff;display:flex;align-items:center;justify-content:center}

/* services */
.section-title{width:1200px;text-align:center;font-size:30px}
.title-rule{width:32px;height:3px;background:var(--red)}
.service-card{position:absolute;width:458px;height:250px;background:var(--card);box-shadow:0 2px 10px rgba(0,0,0,.06)}
.service-card .icon{position:absolute;left:38px;top:40px}
.service-card h3{position:absolute;left:143px;top:38px;font-family:'Poppins',sans-serif;font-weight:600;font-size:18px;color:var(--ink)}
.service-card p{position:absolute;left:143px;top:78px;width:275px;font-size:14.5px;line-height:21px;color:var(--muted)}
.service-card .btn{left:143px;top:190px;width:96px;height:30px;font-size:12px}

/* leadership band */
.lead-title{left:130px;top:1557px;font-size:30px;line-height:50px}
.lead-text{left:133px;top:1673px;width:480px;font-size:18.5px;line-height:28px;color:var(--text)}

/* strategy */
.strategy-title{left:687px;top:2080px;font-size:30px;line-height:44px}
.strategy-title .accent{color:var(--red)}
.strategy-text{left:689px;top:2220px;width:380px;font-size:14.5px;line-height:20.8px;color:var(--muted)}

/* news */
.news-card{position:absolute;top:2719px;width:297px;height:398px;background:var(--card)}
.news-card .thumb{width:297px;height:228px}
.news-card h4{margin:22px 28px 0;font-family:'Poppins',sans-serif;font-weight:600;font-size:17px;line-height:23px;color:var(--ink)}
.news-card p{margin:12px 28px 0;font-size:14.5px;line-height:21px;color:var(--muted)}

/* footer */
.contact-item{top:3327px;display:flex;align-items:center;gap:18px;color:#fff;font-size:15px;line-height:21px}
.contact-dot{width:40px;height:40px;border-radius:50%;background:var(--red);display:flex;align-items:center;justify-content:center;flex:none}
.footer-menu{left:547px;top:3432px;color:#fff}
.footer-menu h5{font-family:'Poppins',sans-serif;font-weight:600;font-size:14px}
.footer-menu ul{list-style:none;display:flex;gap:0;margin-top:10px;font-size:14.5px}
.footer-menu li+li::before{content:"/";margin:0 12px}
.footer-follow{left:130px;top:3563px;display:flex;align-items:center;gap:12px;color:#fff;font-family:'Poppins',sans-serif;font-weight:600;font-size:14px}
.copyright{right:134px;top:3565px;color:#fff;font-size:13px}
</style>
</head>
<body>

<!-- Header -->
<header class="abs site-header">
  <div class="abs brand" style="left:134px;top:36px"><span>BORK VENTURES</span><span class="brand-square"></span></div>
  <div class="abs follow">FOLLOW US <span class="dot fb"></span><span class="dot li"></span></div>
  <div class="abs call-icon">
    <svg width="18" height="18" viewBox="0 0 24 24"><path d="M6.6 10.8a15 15 0 0 0 6.6 6.6l2.2-2.2c.3-.3.7-.4 1-.2 1.1.4 2.3.6 3.6.6.6 0 1 .4 1 1V20c0 .6-.4 1-1 1A17 17 0 0 1 3 4c0-.6.4-1 1-1h3.5c.6 0 1 .4 1 1 0 1.3.2 2.5.6 3.6.1.3 0 .7-.2 1z" fill="#a01c2e"/></svg>
  </div>
  <div class="abs call-label">CALL US NOW</div>
  <div class="abs call-number">301-555-0178</div>
  <nav class="abs main-nav">
    <span class="active">HOME</span><span>ABOUT US</span><span>SERVICES</span><span>STRATEGY</span><span>IT NEWS</span><span>CONTACT US</span>
  </nav>
</header>

<!-- Hero -->
<svg class="abs" style="left:0;top:118px" width="1200" height="600" viewBox="0 0 1200 600">
  <defs>
    <linearGradient id="heroFill" x1="0" y1="0" x2="1" y2="0">
      <stop offset="0" stop-color="#1a2a7a"/><stop offset=".45" stop-color="#2a2440"/><stop offset="1" stop-color="#3a3f5e"/>
    </linearGradient>
  </defs>
  <polygon points="0,0 1200,0 1200,470 600,570 0,470" fill="#a01c2e"/>
  <g role="img" aria-label="Technician working at a server rack in a data centre">
    <polygon points="0,0 1200,0 1200,462 600,558 0,462" fill="url(#heroFill)"/>
  </g>
</svg>
<div class="abs hero-title">NETWORK<br>ASSESSMENT</div>
<div class="btn" style="left:758px;top:392px;width:166px;height:58px;font-size:18px">READ MORE</div>
<div class="abs slide-arrow" style="left:0"><svg width="10" height="16"><path d="M8 2 2 8l6 6" stroke="#333" stroke-width="2" fill="none"/></svg></div>
<div class="abs slide-arrow" style="left:1166px"><svg width="10" height="16"><path d="M2 2l6 6-6 6" stroke="#333" stroke-width="2" fill="none"/></svg></div>
<div class="abs" style="left:556px;top:636px;width:88px;height:88px;border-radius:50%;background:#fff;display:flex;align-items:center;justify-content:center">
  <div style="width:36px;height:36px;background:var(--red)"></div>
</div>

<!-- Services -->
<h2 class="abs heading section-title" style="left:0;top:742px">Our Services</h2>
<div class="abs title-rule" style="left:584px;top:799px"></div>

<div class="service-card" style="left:131px;top:845px">
  <svg class="icon" width="64" height="64" viewBox="0 0 64 64" fill="none" stroke="#a01c2e" stroke-width="2.5"><rect x="14" y="14" width="36" height="36"/><rect x="22" y="22" width="20" height="20"/><circle cx="32" cy="32" r="5"/><path d="M20 4v10M28 4v10M36 4v10M44 4v10M20 50v10M28 50v10M36 50v10M44 50v10M4 20h10M4 28h10M4 36h10M4 44h10M50 20h10M50 28h10M50 36h10M50 44h10"/></svg>
  <h3>Hardware / Software Sales</h3>
  <p>We have access to multiple distributor partners throughout North America, as well as Elite Partner Status with many of the industry's</p>
  <div class="btn">Read More</div>
</div>
<div class="service-card" style="left:611px;top:845px">
  <svg class="icon" width="64" height="64" viewBox="0 0 64 64" fill="none" stroke="#a01c2e" stroke-width="2.5"><circle cx="32" cy="18" r="12"/><path d="M8 62c0-14 10-22 24-22s24 8 24 22z"/><path d="M28 40l4 14 4-14"/></svg>
  <h3>Professional Services</h3>
  <p>Our team provides experienced leadership and guidance, utilizing the industry standard methodologies.</p>
  <div class="btn">Read More</div>
</div>
<div class="service-card" style="left:131px;top:1118px">
  <svg class="icon" width="64" height="72" viewBox="0 0 64 72" fill="none" stroke="#a01c2e" stroke-width="2.5"><rect x="6" y="4" width="52" height="38" rx="2"/><path d="M26 42v10h12V42M20 52h24"/><rect x="40" y="52" width="14" height="18" rx="7"/></svg>
  <h3>Technology Assessment</h3>
  <p>Experience has shown companies that perform objective, third-party technology assessments have proven to be instrumental in identifying</p>
  <div class="btn">Read More</div>
</div>
<div class="service-card" style="left:611px;top:1118px">
  <svg class="icon" width="64" height="64" viewBox="0 0 64 64" fill="none" stroke="#a01c2e" stroke-width="2.5"><path d="M6 6h52v38H22L10 56V44H6z"/><path d="M16 18h32M16 26h32M16 34h24"/></svg>
  <h3>Technology Consulting</h3>
  <p>Implementing quality solutions is more than applying technology to problems. You need experts with deep technical knowledge</p>
  <div class="btn">Read More</div>
</div>

<!-- Leadership band -->
<svg class="abs" style="left:0;top:1403px" width="1200" height="587" viewBox="0 0 1200 587" role="img" aria-label="Two consultants reviewing a folder in a bright server corridor">
  <defs>
    <linearGradient id="bandFill" x1="0" y1="0" x2="1" y2="0">
      <stop offset="0" stop-color="#b8cde3"/><stop offset=".5" stop-color="#dde8f3"/><stop offset="1" stop-color="#9fb7d4"/>
    </linearGradient>
  </defs>
  <polygon points="0,0 600,88 1200,0 1200,587 0,587" fill="url(#bandFill)"/>
</svg>
<h2 class="abs heading lead-title">Bringing Thought Leadership<br>and Quality to Every Project</h2>
<p class="abs lead-text">Bork Ventures, Inc. is an 8(a) full-service IT consulting company based in the Washington, DC Metro area. We offer specialized, highly customized technology solutions for our customers located throughout the United States. Learn about our Services now.</p>
<div class="btn" style="left:134px;top:1844px;width:128px;height:44px;font-size:15px">Read More</div>

<!-- Strategy -->
<div class="abs" style="left:131px;top:2036px;width:502px;height:482px;background:linear-gradient(135deg,#e6e8ea,#cfd5da)" role="img" aria-label="Team meeting around a round table, viewed from above"></div>
<h2 class="abs heading strategy-title"><span class="accent">Our Strategy</span><br>Your Path to Success</h2>
<div class="abs title-rule" style="left:689px;top:2178px"></div>
<p class="abs strategy-text">Civilian and Federal agencies are facing increased demands driven by the changing economic environment and shifts in the way products and services are sold and delivered. These factors have created an imperative to leverage new and innovative technology solution architectures like cloud computing to help reduce cost and deliver profit-driving IT capabilities faster than ever before</p>
<div class="btn" style="left:693px;top:2425px;width:128px;height:44px;font-size:15px">Read More</div>

<!-- IT News -->
<div class="abs" style="left:0;top:2565px;width:1200px;height:740px;background:#eeedef"></div>
<h2 class="abs heading section-title" style="left:0;top:2620px">IT News</h2>
<div class="news-card" style="left:130px">
  <div class="thumb" style="background:linear-gradient(135deg,#c9ced4,#6d7680)" role="img" aria-label="Colleagues working at laptops by a whiteboard"></div>
  <h4>Lorem Ipsum is simply dummy text of the.</h4>
  <p>Lorem ipsum dolor sit amet, cons ectetur adipiscing elit, sed do eiusmod tempor incidid.</p>
</div>
<div class="news-card" style="left:452px">
  <div class="thumb" style="background:linear-gradient(135deg,#a9b3be,#7d8894)" role="img" aria-label="Hands joining two puzzle pieces"></div>
  <h4>Lorem Ipsum is simply dummy text of the.</h4>
  <p>Lorem ipsum dolor sit amet, cons ectetur adipiscing elit, sed do eiusmod tempor incidid.</p>
</div>
<div class="news-card" style="left:774px">
  <div class="thumb" style="background:linear-gradient(135deg,#5d6670,#c8cdd2)" role="img" aria-label="Person taking notes beside a tablet"></div>
  <h4>Lorem Ipsum is simply dummy text of the.</h4>
  <p>Lorem ipsum dolor sit amet, cons ectetur adipiscing elit, sed do eiusmod tempor incidid.</p>
</div>

<!-- Footer -->
<svg class="abs" style="left:0;top:3180px" width="1200" height="457" viewBox="0 0 1200 457">
  <polygon points="0,118 577,26 1200,118 1200,457 0,457" fill="#a01c2e"/>
  <polygon points="0,126 577,34 1200,126 1200,457 0,457" fill="#3a3a3a"/>
  <circle cx="577" cy="26" r="36" fill="#fff"/>
  <rect x="563" y="12" width="28" height="28" fill="#a01c2e"/>
</svg>

<div class="abs contact-item" style="left:130px">
  <span class="contact-dot"><svg width="12" height="16" viewBox="0 0 12 16"><path d="M6 0a6 6 0 0 0-6 6c0 4.5 6 10 6 10s6-5.5 6-10a6 6 0 0 0-6-6zm0 8.2A2.2 2.2 0 1 1 6 3.8a2.2 2.2 0 0 1 0 4.4z" fill="#fff"/></svg></span>
  <span>2280 Harlow Creek Dr<br>Fenwick, MD 20900</span>
</div>
<div class="abs contact-item" style="left:510px">
  <span class="contact-dot"><svg width="14" height="14" viewBox="0 0 24 24"><path d="M6.6 10.8a15 15 0 0 0 6.6 6.6l2.2-2.2c.3-.3.7-.4 1-.2 1.1.4 2.3.6 3.6.6.6 0 1 .4 1 1V20c0 .6-.4 1-1 1A17 17 0 0 1 3 4c0-.6.4-1 1-1h3.5c.6 0 1 .4 1 1 0 1.3.2 2.5.6 3.6.1.3 0 .7-.2 1z" fill="#fff"/></svg></span>
  <span>Call Us now on<br>301-555-0178</span>
</div>
<div class="abs contact-item" style="left:818px">
  <span class="contact-dot"><svg width="14" height="11" viewBox="0 0 14 11"><rect width="14" height="11" rx="1" fill="#fff"/><path d="M1 1l6 5 6-5" stroke="#a01c2e" stroke-width="1.4" fill="none"/></svg></span>
  <span>E mail us<br>info@borkventuresinc.example</span>
</div>

<div class="abs" style="left:130px;top:3396px;width:940px;height:1px;background:var(--rule)"></div>
<div class="abs" style="left:475px;top:3396px;width:1px;height:110px;background:var(--rule)"></div>

<div class="abs brand" style="left:132px;top:3432px;color:#fff"><span>BORK VENTURES</span><span class="brand-square" style="background:#fff"></span></div>

<div class="abs footer-menu">
  <h5>MENU</h5>
  <ul><li>Home</li><li>About us</li><li>Services</li><li>Strategy</li><li>IT News</li><li>Contact us</li></ul>
</div>

<div class="abs footer-follow">FOLLOW US <span class="dot fb"></span><span class="dot li"></span></div>
<div class="abs copyright">Copyright 2019 All Rights Reserved</div>

</body>
</html>
```